Business cards to launch an education platform

Hi,
I am looking at having new business cards designed.
I am a startup, developing a web platform for schools and university, the education world. It's an online assessment system.
I would like a card that looks classy, and that is using the colors and the font of my logo.

I have attached:
1) my logo
2) A business card that I have designed quickly so you can have all the information required in the card, but I really don't like it.
3) The font that I am using (Lato Regular) to design my web platform
4) Some screenshots of my web platform so you can have a look at the style that I have.

Target Market(s)

Major market: Education system: Schools and university
Minor markets: Business in general

Industry/Entity Type

Business

Contact Information for Business Card

Clara Fenwick
Director

M: 0437 518 902
E: clara.fenwick@amberLoomSystems.com.au

Requirements
Must have
• The colors of my logo

```html
<!DOCTYPE html>
<html lang="en">
<head>
<meta charset="UTF-8">
<title>Amber Loom Systems – Business Cards</title>
<link rel="stylesheet" href="https://fonts.googleapis.com/css2?family=Lato:wght@300;400&family=Arimo:wght@400;700&display=swap">
<style>
  :root {
    --canvas: #d9d6d0;
    --card-black: #0b0b0c;
    --card-black-soft: #1a1b1d;
    --brand-blue: #2a8fd0;
    --brand-blue-light: #3bb3de;
    --brand-blue-deep: #1a6fae;
    --divider: #2fc3e6;
    --white: #f4f4f4;
  }
  * { margin: 0; padding: 0; box-sizing: border-box; }
  html, body {
    width: 1200px; height: 892px; overflow: hidden;
    background: var(--canvas);
  }
  .sheet {
    width: 1200px; height: 892px;
    display: flex; flex-direction: column;
    align-items: center; justify-content: center; gap: 40px;
  }
  .card {
    position: relative;
    width: 700px; height: 400px;
    background: linear-gradient(150deg, var(--card-black-soft) 0%, var(--card-black) 55%);
    overflow: hidden;
  }
  .card__band {
    position: absolute; left: 0; right: 0; height: 34px;
    background: linear-gradient(180deg, var(--brand-blue-light), var(--brand-blue-deep));
  }
  .card--front .card__band { bottom: 0; }
  .card--back .card__band { top: 0; }

  /* Front */
  .brand {
    position: absolute; left: 44px; top: 150px;
    display: flex; align-items: center; gap: 14px;
  }
  .brand__mark {
    width: 40px; height: 40px; background: var(--brand-blue);
  }
  .brand__name {
    font-family: "Lato", sans-serif; font-weight: 300;
    color: var(--brand-blue); font-size: 24px; line-height: 1.15;
    letter-spacing: 2px; text-transform: uppercase;
  }
  .divider {
    position: absolute; left: 302px; top: 60px;
    width: 1px; height: 250px; background: var(--divider);
  }
  .contact {
    position: absolute; left: 336px; top: 82px; right: 20px;
    font-family: "Arimo", sans-serif;
  }
  .contact__name {
    color: var(--brand-blue); font-weight: 700; font-size: 42px;
    letter-spacing: 1px; line-height: 1; white-space: nowrap;
  }
  .contact__role {
    color: var(--white); font-weight: 700; font-size: 22px;
    margin-top: 6px;
  }
  .contact__list { list-style: none; margin-top: 34px; }
  .contact__item {
    display: flex; align-items: center; gap: 12px;
    color: var(--white); font-size: 16px; margin-bottom: 14px;
    white-space: nowrap;
  }
  .contact__icon { width: 16px; height: 16px; flex: none; }

  /* Back */
  .back-brand {
    position: absolute; left: 0; right: 0; top: 34px; bottom: 0;
    display: flex; align-items: center; justify-content: center; gap: 26px;
  }
  .back-brand__mark { width: 88px; height: 88px; background: var(--white); }
  .back-brand__name {
    font-family: "Lato", sans-serif; font-weight: 300;
    color: var(--white); font-size: 40px; line-height: 1.15;
    letter-spacing: 4px; text-transform: uppercase;
  }
</style>
</head>
<body>
<main class="sheet">
  <section class="card card--front" aria-label="Business card front">
    <div class="brand">
      <span class="brand__mark"></span>
      <span class="brand__name">Amber Loom<br>Systems</span>
    </div>
    <div class="divider"></div>
    <div class="contact">
      <p class="contact__name">Clara Fenwick</p>
      <p class="contact__role">Director</p>
      <ul class="contact__list">
        <li class="contact__item">
          <svg class="contact__icon" viewBox="0 0 16 16" aria-hidden="true">
            <rect width="16" height="16" fill="var(--brand-blue)"/>
            <path d="M5 3.5c.6 0 1.4 1.6 1.4 2.2 0 .5-.8.8-.8 1.2 0 .9 1.6 2.6 2.6 2.6.4 0 .7-.8 1.2-.8.6 0 2.2.8 2.2 1.4 0 1-1 2.3-2.2 2.3C6.6 12.4 3.6 9.4 3.6 6.6 3.6 4.5 4.3 3.5 5 3.5z" fill="var(--white)"/>
          </svg>
          <span>0437 518 902</span>
        </li>
        <li class="contact__item">
          <svg class="contact__icon" viewBox="0 0 16 16" aria-hidden="true">
            <rect width="16" height="16" fill="var(--brand-blue)"/>
            <rect x="3" y="4.5" width="10" height="7" fill="none" stroke="var(--white)" stroke-width="1.2"/>
            <path d="M3 4.5l5 4 5-4" fill="none" stroke="var(--white)" stroke-width="1.2"/>
          </svg>
          <span>clara.fenwick@amberLoomSystems.com.au</span>
        </li>
      </ul>
    </div>
    <div class="card__band"></div>
  </section>

  <section class="card card--back" aria-label="Business card back">
    <div class="card__band"></div>
    <div class="back-brand">
      <span class="back-brand__mark"></span>
      <span class="back-brand__name">Amber Loom<br>Systems</span>
    </div>
  </section>
</main>
</body>
</html>
```